Simple but elegant business card/logo design for exclusive beauty business

We need a logo designed for a new elegant and exclusive beauty business called "G". The logo itself should be a stylistic and custom design for the letter "G". We would like the business card to have the logo as the centrepiece on a clean background. Gold Logo on black background or silver on white background.

The business card details should be displayed centre of the card. Details are as follows:

Marla Vance
Facebook: /simplyshinebym
Instagram: /simplyshinebym

The words "Simply Shine" should also appear somewhere on the card.

Industry/Entity Type

Business

Logo Text

G

Requirements
Must have
• Design must be simple, clean and elegant
Should not have
• The design should not be cluttered

```html
<!DOCTYPE html>
<html lang="en">
<head>
<meta charset="utf-8">
<title>Simply Shine – Business Card</title>
<link href="https://fonts.googleapis.com/css2?family=Open+Sans:wght@300;400;600&display=swap" rel="stylesheet">
<style>
  :root {
    --backdrop: #1f1f1f;
    --card: #ffffff;
    --silver: #8c8c8c;
    --silver-light: #b4b4b4;
    --silver-dark: #6e6e6e;
    --rule: #d2d2d2;
  }
  * { margin: 0; padding: 0; box-sizing: border-box; }
  html, body {
    width: 1200px;
    height: 660px;
    overflow: hidden;
    background: var(--backdrop);
    font-family: "Open Sans", Arial, sans-serif;
  }
  .canvas {
    width: 1200px;
    height: 660px;
    display: flex;
    align-items: center;
    justify-content: center;
    gap: 40px;
  }
  .card {
    width: 540px;
    height: 300px;
    background: var(--card);
    position: relative;
    box-shadow: 0 8px 24px rgba(0,0,0,0.45);
  }
  /* Front */
  .card--front {
    display: flex;
    align-items: center;
    justify-content: center;
  }
  .brand-mark {
    display: flex;
    align-items: center;
    gap: 12px;
    color: var(--silver);
    font-weight: 400;
    font-size: 30px;
    letter-spacing: 0.5px;
  }
  .brand-mark__dot {
    width: 14px;
    height: 14px;
    border-radius: 50%;
    background: var(--silver);
  }
  /* Back */
  .card--back {
    display: flex;
    align-items: center;
  }
  .back__brand {
    width: 270px;
    display: flex;
    justify-content: center;
    padding-top: 60px;
  }
  .back__brand .brand-mark {
    font-size: 26px;
  }
  .back__rule {
    position: absolute;
    left: 262px;
    top: 60px;
    width: 1px;
    height: 170px;
    background: var(--rule);
    transform: rotate(-14deg);
    transform-origin: top center;
  }
  .contact {
    padding-left: 40px;
    color: var(--silver);
  }
  .contact__name {
    font-size: 20px;
    font-weight: 300;
    color: var(--silver-light);
    margin-bottom: 6px;
  }
  .contact__name strong {
    font-weight: 600;
    color: var(--silver);
  }
  .contact__list {
    list-style: none;
    font-size: 12.5px;
    letter-spacing: 0.3px;
  }
  .contact__list li {
    display: flex;
    align-items: center;
    gap: 10px;
    height: 19px;
  }
  .contact__list li.contact__gap { margin-top: 14px; }
  .contact__icon {
    width: 13px;
    height: 13px;
    flex: none;
  }
  .contact__icon--plain {
    width: 11px;
    height: 11px;
    margin: 0 1px;
    background: var(--silver-dark);
    border-radius: 2px;
  }
</style>
</head>
<body>
<main class="canvas">
  <section class="card card--front" aria-label="Card front">
    <div class="brand-mark">
      <span class="brand-mark__dot"></span>
      <span class="brand-mark__name">Simply Shine</span>
    </div>
  </section>

  <section class="card card--back" aria-label="Card back">
    <div class="back__brand">
      <div class="brand-mark">
        <span class="brand-mark__name">Simply Shine</span>
      </div>
    </div>
    <div class="back__rule"></div>
    <div class="contact">
      <p class="contact__name"><strong>Marla</strong> Vance</p>
      <ul class="contact__list">
        <li>
          <svg class="contact__icon" viewBox="0 0 13 13" aria-hidden="true">
            <rect x="3" y="0.5" width="7" height="12" rx="1.2" fill="none" stroke="#6e6e6e" stroke-width="1.3"/>
            <circle cx="6.5" cy="10.2" r="0.8" fill="#6e6e6e"/>
          </svg>
          <span>0400 555 019</span>
        </li>
        <li>
          <svg class="contact__icon" viewBox="0 0 13 13" aria-hidden="true">
            <rect x="0.5" y="2.5" width="12" height="8" fill="none" stroke="#6e6e6e" stroke-width="1.2"/>
            <path d="M0.5 2.5 L6.5 7 L12.5 2.5" fill="none" stroke="#6e6e6e" stroke-width="1.2"/>
          </svg>
          <span>simplyshinebym@mail.com</span>
        </li>
        <li class="contact__gap">
          <span class="contact__icon contact__icon--plain"></span>
          <span>/simplyshinebym</span>
        </li>
        <li>
          <span class="contact__icon contact__icon--plain"></span>
          <span>/simplyshinebym</span>
        </li>
      </ul>
    </div>
  </section>
</main>
</body>
</html>
```